Wealth Education Business Needs Sharp Business Card Design

We need a business card design for a recently launched investor education business called Harbor Crest.

The final design should promote security, empowerment, self improvement and financial gain. The card will ideally promote the stature of the business.

For more information and colours please visit harborcrest.com.au

Target Market(s)

Corporate executives and high net worth individuals

Industry/Entity Type

Education

Contact Information for Business Card

```html
<!DOCTYPE html>
<html lang="en">
<head>
<meta charset="utf-8">
<title>Harbor Crest – Business Card</title>
<link rel="stylesheet" href="https://fonts.googleapis.com/css2?family=Josefin+Sans:wght@600&family=Lato:wght@400;700&display=swap">
<style>
  :root {
    --backdrop: #ebebeb;
    --card-white: #ffffff;
    --green-light: #7fba5a;
    --green-deep: #62a03f;
    --ink: #3a3a3a;
    --name-blue: #1c4f6b;
    --text-dark: #1f2a22;
  }
  html, body {
    margin: 0;
    width: 1200px;
    height: 720px;
    overflow: hidden;
    background: var(--backdrop);
  }
  .canvas {
    position: relative;
    width: 1200px;
    height: 720px;
  }
  .card {
    position: absolute;
    top: 241px;
    width: 419px;
    height: 239px;
    border-radius: 12px;
    overflow: hidden;
    background: var(--card-white);
  }
  .card--front { left: 148px; }
  .card--back  { left: 633px; }

  .front-field {
    position: absolute;
    inset: 0;
  }
  .front-content {
    position: absolute;
    left: 17px;
    top: 0;
    font-family: "Lato", sans-serif;
    color: var(--text-dark);
  }
  .wordmark {
    font-family: "Josefin Sans", sans-serif;
    font-weight: 600;
    color: var(--ink);
    letter-spacing: 0.16em;
    white-space: nowrap;
  }
  .wordmark--small {
    position: absolute;
    top: 28px;
    font-size: 13px;
  }
  .person-name {
    position: absolute;
    top: 70px;
    margin: 0;
    font-size: 15.5px;
    font-weight: 700;
    color: var(--name-blue);
    white-space: nowrap;
  }
  .person-role {
    position: absolute;
    top: 90px;
    margin: 0;
    font-size: 11px;
    white-space: nowrap;
  }
  .contact-list {
    position: absolute;
    top: 121px;
    margin: 0;
    padding: 0;
    list-style: none;
    font-size: 11px;
    line-height: 15px;
    white-space: nowrap;
  }
  .contact-list li {
    display: flex;
    align-items: center;
    gap: 5px;
  }
  .contact-icon {
    width: 9px;
    height: 9px;
    flex: none;
  }
  .address {
    position: absolute;
    top: 195px;
    display: flex;
    gap: 5px;
    font-size: 11px;
    line-height: 15px;
    font-style: normal;
    white-space: nowrap;
  }
  .address .contact-icon { margin-top: 2px; }

  .wordmark--large {
    position: absolute;
    left: 0;
    right: 0;
    top: 100px;
    text-align: center;
    font-size: 38px;
    letter-spacing: 0.2em;
    padding-left: 0.2em;
  }
</style>
</head>
<body>
<main class="canvas">

  <section class="card card--front" aria-label="Business card front">
    <svg class="front-field" viewBox="0 0 419 239" width="419" height="239" aria-hidden="true">
      <defs>
        <linearGradient id="field-green" x1="0" y1="0" x2="1" y2="1">
          <stop offset="0" stop-color="var(--green-light)"/>
          <stop offset="1" stop-color="var(--green-deep)"/>
        </linearGradient>
      </defs>
      <path d="M0 0 H250 C215 60 215 180 250 239 H0 Z" fill="url(#field-green)"/>
    </svg>

    <div class="front-content">
      <div class="wordmark wordmark--small">HARBOR CREST</div>
      <h1 class="person-name">Marcus Hale</h1>
      <p class="person-role">Director</p>
      <ul class="contact-list">
        <li>
          <svg class="contact-icon" viewBox="0 0 10 10" aria-hidden="true"><path d="M1 3 Q5 0 9 3 L8 4.5 6.5 3.8 V3 H3.5 V3.8 L2 4.5 Z M2.5 5 H7.5 L8.5 9 H1.5 Z" fill="var(--name-blue)"/></svg>
          1300 555 014
        </li>
        <li>
          <svg class="contact-icon" viewBox="0 0 10 10" aria-hidden="true"><rect x="2.5" y="0.5" width="5" height="9" rx="1" fill="none" stroke="var(--name-blue)" stroke-width="1.2"/></svg>
          +613 5550 2718
        </li>
        <li>
          <svg class="contact-icon" viewBox="0 0 10 10" aria-hidden="true"><rect x="0.5" y="2" width="9" height="6.5" fill="var(--name-blue)"/><path d="M0.5 2 L5 5.5 L9.5 2" fill="none" stroke="var(--green-light)" stroke-width="0.8"/></svg>
          support@harborcrest.com.au
        </li>
        <li>
          <svg class="contact-icon" viewBox="0 0 10 10" aria-hidden="true"><g fill="none" stroke="var(--name-blue)" stroke-width="0.9"><circle cx="5" cy="5" r="4.3"/><ellipse cx="5" cy="5" rx="1.8" ry="4.3"/><path d="M0.7 5 H9.3"/></g></svg>
          www.harborcrest.com.au
        </li>
      </ul>
      <address class="address">
        <svg class="contact-icon" viewBox="0 0 10 10" aria-hidden="true"><path d="M5 0.8 L9.5 5 H8 V9.3 H6 V6.5 H4 V9.3 H2 V5 H0.5 Z" fill="var(--name-blue)"/></svg>
        <span>Level 5, 42 Garden Row,<br>Melbourne VIC 3000</span>
      </address>
    </div>
  </section>

  <section class="card card--back" aria-label="Business card back">
    <div class="wordmark wordmark--large">HARBOR CREST</div>
  </section>

</main>
</body>
</html>
```